Tree Service Billboard 20x8 ft

We need a billboard design for a tree service company.
The billboard is 20ft x 8 ft so we need a design that is capable to stretching to those dimensions without loosing quality.
I have attached a series of images.
Image 1- Simply a billboard that I think looks good that I would like you to use for inspiration. I am aiming for the same format only no color in the wording, just black white, or gray. I like the the trees in the background, the logo placed to the left, and wording on the right.
Image 2- Current Logo I would like to the left of the billboard
Image 3- Another format of current logo if needed.
Image 4- A drawn out design template
Image 5- Another drawn out design template

Specific things I am looking for
-The contact number to be the largest thing on the design
-The logo on the design
-Key points to the design to say:
Tree Removal
Tree Trimming
Land Development
Stump Grinding
Storm Response
Insured
Free Bids
-The facebook logo
-The Google Logo

```html
<!DOCTYPE html>
<html lang="en">
<head>
<meta charset="utf-8">
<title>Tree Service Billboard 20x8 ft</title>
<link href="https://fonts.googleapis.com/css2?family=Bebas+Neue&family=Montserrat:wght@500;700;800&display=swap" rel="stylesheet">
<style>
  :root {
    --page-bg: #f2f2f2;
    --ink: #000000;
    --paper: #ffffff;
    --steel: #666666;
    --forest-dark: #1f3a22;
    --forest-mid: #3c6a35;
    --forest-mist: #7f9a86;
  }
  * { margin: 0; padding: 0; box-sizing: border-box; }
  html, body { width: 1200px; height: 833px; overflow: hidden; }
  body { background: var(--page-bg); position: relative; font-family: "Montserrat", sans-serif; }

  .sheet-title {
    position: absolute; top: 152px; left: 0; width: 1200px;
    text-align: center; font-family: "Montserrat", sans-serif; font-weight: 500;
    font-size: 47px; letter-spacing: 0; color: var(--ink); white-space: nowrap;
  }

  .billboard {
    position: absolute; left: 63px; top: 240px; width: 1074px; height: 429px; overflow: hidden;
  }
  .billboard-shapes { position: absolute; inset: 0; }

  .brand-mark {
    position: absolute; left: 180px; top: 32px; width: 182px; height: 180px;
    border-radius: 50%; background: var(--paper); border: 6px solid var(--ink);
    box-shadow: 0 0 0 4px var(--paper);
  }
  .brand-name {
    position: absolute; left: 40px; top: 222px; width: 474px; text-align: center;
    font-family: "Bebas Neue", sans-serif; font-size: 60px; line-height: 1;
    color: var(--paper); white-space: nowrap;
  }

  .phone {
    position: absolute; left: 83px; top: 318px;
    font-family: "Bebas Neue", sans-serif; font-size: 92px; line-height: 1;
    letter-spacing: 1.5px; color: var(--paper); white-space: nowrap;
  }
  .social-dot {
    position: absolute; top: 339px; width: 40px; height: 40px; border-radius: 50%;
    border: 3px solid var(--paper);
  }
  .social-dot.first { left: 527px; }
  .social-dot.second { left: 581px; }

  .services {
    position: absolute; right: 36px; top: 48px; list-style: none; text-align: right;
    font-family: "Bebas Neue", sans-serif; font-size: 50px; line-height: 56px;
    color: var(--ink); letter-spacing: -0.5px; white-space: nowrap;
  }

  .insured-badge { position: absolute; left: 817px; top: 326px; width: 222px; height: 84px; }
  .insured-pill {
    position: absolute; left: 60px; top: 11px; width: 160px; height: 60px;
    background: var(--ink); border-radius: 30px; color: var(--paper);
    font-family: "Montserrat", sans-serif; font-weight: 800; font-size: 21px; line-height: 21px;
    display: flex; flex-direction: column; align-items: flex-end; justify-content: center; padding-right: 20px;
  }
  .insured-pill span:first-child { padding-right: 20px; }
  .insured-shield { position: absolute; left: 0; top: 0; width: 70px; height: 84px; }
</style>
</head>
<body>
  <h1 class="sheet-title">TREE SERVICE BILLBOARD 20X8 FT</h1>

  <section class="billboard">
    <svg class="billboard-shapes" width="1074" height="429" viewBox="0 0 1074 429">
      <defs>
        <linearGradient id="forestTone" x1="0" y1="0" x2="0" y2="1">
          <stop offset="0" stop-color="var(--forest-mist)"/>
          <stop offset="0.35" stop-color="var(--forest-mid)"/>
          <stop offset="1" stop-color="var(--forest-dark)"/>
        </linearGradient>
      </defs>
      <rect class="forest-photo" x="0" y="0" width="1074" height="307" fill="url(#forestTone)" role="img" aria-label="Photo of a misty evergreen forest"/>
      <rect class="phone-band" x="0" y="307" width="820" height="107" fill="var(--ink)"/>
      <rect class="base-strip" x="0" y="414" width="820" height="15" fill="var(--steel)"/>
      <path class="info-panel-shadow" d="M798 0 C 700 60, 660 170, 684 260 C 705 340, 750 400, 801 429 L 1074 429 L 1074 0 Z" fill="var(--steel)"/>
      <path class="info-panel" d="M809 0 C 715 60, 678 170, 697 260 C 716 340, 760 400, 812 429 L 1074 429 L 1074 0 Z" fill="var(--paper)"/>
    </svg>

    <div class="brand-mark" role="img" aria-label="Company logo area"></div>
    <div class="brand-name">Birchline Tree Service</div>

    <div class="phone">555-014-2387</div>
    <span class="social-dot first" aria-label="Social page"></span>
    <span class="social-dot second" aria-label="Reviews page"></span>

    <ul class="services">
      <li>Tree Removal</li>
      <li>Tree Trimming</li>
      <li>Land Development</li>
      <li>Stump Grinding</li>
      <li>Storm Response</li>
    </ul>

    <div class="insured-badge">
      <div class="insured-pill"><span>FULLY</span><span>INSURED</span></div>
      <svg class="insured-shield" viewBox="0 0 70 84">
        <path d="M35 2 L44 9 L68 6 L68 48 C68 66 50 76 35 82 C20 76 2 66 2 48 L2 6 L26 9 Z" fill="var(--ink)" stroke="var(--paper)" stroke-width="2"/>
        <path d="M15 42 L29 56 L55 24" fill="none" stroke="var(--paper)" stroke-width="7" stroke-linecap="round" stroke-linejoin="round"/>
      </svg>
    </div>
  </section>
</body>
</html>
```